Bram Keystone Homes needs a business card

We need a business card for a new company in Canada, Ontario. Our company is all about luxury contraction homes for our clients. Our product and services are custom projects design. Under the business logo that will be created, we want a slogan that will be a memorable phrase for consumers to remember us to tell their friends and relatives.

Additional infomation
- Ludovic Entrasse
- President / Ceo
-519.604.3087

Find point what luxury construction products and services can be done

We like to see colors:
- #663300
- and something other colors or color that would attract the client needs and wants

The final design should communicate leads from new or old clients that will grow our empire. Most of all, we try to work among the budget that clients want

NOTE
- we also need an icon for the business (Example: Instagram, Facebook, and Whatsapp icons)
- We want the company name to be remembered easily for clients and our distributors who would get our orders.
- we need an icon on the business cards: Facebook and Instagram.

Thanks,
Bram Keystone Homes

```html
<!DOCTYPE html>
<html lang="en">
<head>
<meta charset="utf-8">
<title>Bram Keystone Homes – Business Card</title>
<link href="https://fonts.googleapis.com/css2?family=Roboto:wght@400;500;700;900&family=Lato:wght@400&display=swap" rel="stylesheet">
<style>
  :root {
    --backdrop: #2e2e2e;
    --brand-brown: #663300;
    --card-white: #ffffff;
    --ink: #222222;
    --rule: #555555;
    --social-blue: #2f5d9a;
  }
  * { margin: 0; padding: 0; box-sizing: border-box; }
  html, body {
    width: 1200px; height: 1200px; overflow: hidden;
    background: var(--backdrop);
  }
  .canvas { position: relative; width: 1200px; height: 1200px; }

  .card {
    position: absolute; top: 310px; width: 366px; height: 594px;
  }
  .card--front { left: 233px; background: var(--card-white); }
  .card--back { left: 628px; background: var(--brand-brown); }

  .wordmark {
    font-family: 'Roboto', sans-serif; font-weight: 900;
    letter-spacing: -0.3px; white-space: nowrap;
  }
  .tagline {
    font-family: 'Roboto', sans-serif; font-weight: 400;
    white-space: nowrap; text-transform: uppercase;
  }

  .card--front .brand {
    position: absolute; top: 198px; left: 0; width: 100%; text-align: center;
    color: var(--brand-brown);
  }
  .card--front .wordmark { font-size: 27px; line-height: 32px; }
  .card--front .tagline { font-size: 11.5px; line-height: 16px; margin-top: 2px; }

  .contact {
    position: absolute; top: 390px; left: 0; width: 100%; text-align: center;
  }
  .contact__name {
    font-family: 'Roboto', sans-serif; font-weight: 500; font-size: 25px;
    color: var(--brand-brown); line-height: 30px;
  }
  .contact__title {
    font-family: 'Lato', sans-serif; font-size: 21px; color: var(--ink); line-height: 24px;
  }
  .contact__rule {
    width: 228px; height: 1px; background: var(--rule); margin: 18px auto 0;
  }
  .contact__phone {
    font-family: 'Lato', sans-serif; font-size: 25px; color: var(--ink);
    margin-top: 16px; line-height: 30px; letter-spacing: 0.3px;
  }
  .social { display: block; margin: 14px auto 0; }

  .card--back .brand {
    position: absolute; left: 50%; top: 50%;
    transform: translate(-50%, -50%) rotate(-90deg);
    text-align: center; color: var(--card-white);
    margin-left: 2px;
  }
  .card--back .wordmark { font-size: 37px; line-height: 42px; }
  .card--back .tagline { font-size: 15px; line-height: 20px; margin-top: 2px; letter-spacing: 0.2px; }
</style>
</head>
<body>
<main class="canvas">
  <section class="card card--front">
    <div class="brand">
      <div class="wordmark">Bram Keystone Homes</div>
      <div class="tagline">- Home Renovations - Custom Project Design -</div>
    </div>
    <div class="contact">
      <div class="contact__name">LUDOVIC ENTRASSE</div>
      <div class="contact__title">President / CEO</div>
      <div class="contact__rule"></div>
      <div class="contact__phone">519.604.3087</div>
      <svg class="social" width="230" height="30" viewBox="0 0 230 30" role="img" aria-label="Social media links">
        <line x1="0" y1="15" x2="82" y2="15" stroke="#555555" stroke-width="1"/>
        <line x1="148" y1="15" x2="230" y2="15" stroke="#555555" stroke-width="1"/>
        <circle cx="98" cy="15" r="13" fill="#2f5d9a"/>
        <circle cx="131" cy="15" r="13" fill="#2f5d9a"/>
      </svg>
    </div>
  </section>

  <section class="card card--back">
    <div class="brand">
      <div class="wordmark">Bram Keystone Homes</div>
      <div class="tagline">- Home Renovations - Custom Project Design -</div>
    </div>
  </section>
</main>
</body>
</html>
```